Parcelwise HQ letterhead and envelope

Design a formal (8.5x11) letterhead and envelope for sales outreach and legal matters. Using design input from https://www.parcelwisehq.example/ and the attached documents.

Industry/Entity Type

Software Service

Requirements
Must have
• These 4 hex colors are our official colors:
• #355c98 [blue]
• #1eb1a2 [teal]
• #fdba12 [gold]
• #f1653b [orange]
• So no other colors besides these should be used.

```html
<!DOCTYPE html>
<html lang="en">
<head>
<meta charset="utf-8">
<title>Parcelwise HQ Letterhead</title>
<link href="https://fonts.googleapis.com/css2?family=Open+Sans:wght@400;600&display=swap" rel="stylesheet">
<style>
  :root {
    --brand-blue: #355c98;
    --soft-lilac: #d9dbea;
    --ink-grey: #4a4a4a;
    --paper: #ffffff;
  }
  * { margin: 0; padding: 0; box-sizing: border-box; }
  html, body { width: 927px; height: 1200px; overflow: hidden; background: var(--paper); }
  .letterhead {
    position: relative;
    width: 927px;
    height: 1200px;
    background: var(--paper);
    font-family: "Open Sans", Arial, sans-serif;
    overflow: hidden;
  }
  .top-band { position: absolute; top: 0; left: 0; width: 927px; height: 31px; }
  .brand {
    position: absolute;
    left: 54px;
    top: 70px;
    display: flex;
    align-items: center;
    gap: 20px;
    color: var(--brand-blue);
  }
  .brand-dot {
    width: 60px; height: 60px;
    border-radius: 50%;
    background: var(--brand-blue);
  }
  .brand-name {
    font-size: 48px;
    font-weight: 400;
    letter-spacing: 0.5px;
    line-height: 1;
  }
  .sender {
    position: absolute;
    right: 55px;
    top: 66px;
    text-align: right;
    color: var(--brand-blue);
    font-weight: 600;
    font-size: 20.5px;
    line-height: 26px;
  }
  .backdrop-disc {
    position: absolute;
    left: 512px;
    top: 617px;
    width: 424px;
    height: 424px;
    border-radius: 50%;
    background: var(--soft-lilac);
    opacity: 0.55;
  }
  .footer-rule {
    position: absolute;
    left: 2px;
    top: 1053px;
    width: 925px;
    height: 2px;
    background: var(--brand-blue);
  }
  .contact {
    position: absolute;
    left: 0;
    top: 1059px;
    width: 965px;
    text-align: center;
    color: var(--ink-grey);
    font-size: 14.5px;
    line-height: 22.8px;
    font-style: normal;
  }
  .bottom-band {
    position: absolute;
    left: 0;
    top: 1181px;
    width: 927px;
    height: 19px;
    background: var(--brand-blue);
  }
</style>
</head>
<body>
<div class="letterhead">
  <svg class="top-band" viewBox="0 0 927 31" aria-hidden="true">
    <polygon points="0,0 676,0 640,31 0,31" fill="#355c98"/>
    <polygon points="680,31 716,0 689,0 653,31" fill="#355c98" opacity="0"/>
    <polygon points="655,31 694,0 705,0 666,31" fill="#355c98"/>
    <polygon points="677,31 716,0 716,0 677,31" fill="#355c98"/>
    <polygon points="677,31 712,0 716,0 681,31" fill="#355c98" opacity="0"/>
    <polygon points="675,31 713,0 717,0 717,0 679,31" fill="#355c98" opacity="0"/>
    <polygon points="676,31 714,0 718,0 702,31" fill="#355c98" opacity="0"/>
    <polygon points="677,31 715,0 717,0 717,0 702,31" fill="#355c98" opacity="0"/>
    <polygon points="677,31 714,0 717,0 704,31" fill="#355c98" opacity="0"/>
    <polygon points="678,31 715,0 718,0 681,31" fill="#355c98" opacity="0"/>
    <polygon points="676,31 714,0 717,0 679,31" fill="#355c98" opacity="0"/>
    <polygon points="676,31 714,0 717,0 679,31" fill="#355c98" opacity="0"/>
    <polygon points="676,31 714,0 717,0 679,31" fill="#355c98" opacity="0"/>
    <polygon points="677,31 715,0 716,0 700,31" fill="#355c98" opacity="0"/>
    <polygon points="680,31 716,0 716,0 700,31" fill="#355c98" opacity="0"/>
    <polygon points="676,31 714,0 718,0 702,31" fill="#355c98" opacity="0"/>
    <polygon points="679,31 716,0 718,0 703,31" fill="#355c98" opacity="0"/>
    <polygon points="676,31 713,0 717,0 702,31" fill="#355c98" opacity="0"/>
    <polygon points="680,31 716,0 717,0 702,31" fill="#355c98" opacity="0"/>
    <polygon points="676,31 714,0 717,0 701,31" fill="#355c98" opacity="0"/>
    <polygon points="676,31 714,0 717,0 703,31" fill="#355c98" opacity="0"/>
    <polygon points="679,31 716,0 718,0 702,31" fill="#355c98" opacity="0"/>
    <polygon points="677,31 715,0 717,0 703,31" fill="#355c98" opacity="0"/>
    <polygon points="676,31 714,0 717,0 702,31" fill="#355c98" opacity="0"/>
    <polygon points="680,31 716,0 717,0 703,31" fill="#355c98" opacity="0"/>
    <polygon points="676,31 714,0 718,0 702,31" fill="#355c98" opacity="0"/>
    <polygon points="677,31 715,0 717,0 702,31" fill="#355c98" opacity="0"/>
    <polygon points="676,31 714,0 717,0 702,31" fill="#355c98" opacity="0"/>
    <polygon points="676,31 714,0 717,0 702,31" fill="#355c98" opacity="0"/>
    <polygon points="676,31 714,0 717,0 702,31" fill="#355c98" opacity="0"/>
    <polygon points="676,31 714,0 717,0 702,31" fill="#355c98" opacity="0"/>
    <polygon points="676,31 714,0 717,0 702,31" fill="#355c98" opacity="0"/>
    <polygon points="678,31 715,0 717,0 702,31" fill="#355c98" opacity="0"/>
    <polygon points="678,31 715,0 717,0 702,31" fill="#355c98" opacity="0"/>
    <polygon points="676,31 714,0 717,0 702,31" fill="#355c98" opacity="0"/>
    <polygon points="676,31 714,0 717,0 702,31" fill="#355c98" opacity="0"/>
    <polygon points="676,31 714,0 717,0 702,31" fill="#355c98" opacity="0"/>
    <polygon points="676,31 714,0 717,0 702,31" fill="#355c98" opacity="0"/>
    <polygon points="676,31 714,0 717,0 702,31" fill="#355c98" opacity="0"/>
    <polygon points="676,31 714,0 717,0 702,31" fill="#355c98" opacity="0"/>
    <polygon points="676,31 714,0 717,0 702,31" fill="#355c98" opacity="0"/>
    <polygon points="678,31 714,0 716,0 702,31" fill="#355c98" opacity="0"/>
    <polygon points="676,31 714,0 717,0 702,31" fill="#355c98" opacity="0"/>
    <polygon points="676,31 714,0 717,0 702,31" fill="#355c98" opacity="0"/>
    <polygon points="678,31 714,0 717,0 702,31" fill="#355c98" opacity="0"/>
    <polygon points="676,31 714,0 717,0 702,31" fill="#355c98" opacity="0"/>
    <polygon points="676,31 714,0 717,0 702,31" fill="#355c98" opacity="0"/>
    <polygon points="676,31 714,0 717,0 702,31" fill="#355c98" opacity="0"/>
    <polygon points="676,31 714,0 717,0 702,31" fill="#355c98" opacity="0"/>
    <polygon points="676,31 714,0 717,0 702,31" fill="#355c98" opacity="0"/>
    <polygon points="676,31 714,0 717,0 702,31" fill="#355c98" opacity="0"/>
    <polygon points="676,31 714,0 717,0 702,31" fill="#355c98" opacity="0"/>
    <polygon points="676,31 714,0 717,0 702,31" fill="#355c98" opacity="0"/>
    <polygon points="676,31 714,0 717,0 702,31" fill="#355c98" opacity="0"/>
    <polygon points="676,31 714,0 717,0 702,31" fill="#355c98" opacity="0"/>
    <polygon points="676,31 714,0 717,0 702,31" fill="#355c98" opacity="0"/>
    <polygon points="676,31 714,0 717,0 702,31" fill="#355c98" opacity="0"/>
    <polygon points="676,31 714,0 717,0 702,31" fill="#355c98" opacity="0"/>
    <polygon points="676,31 714,0 717,0 702,31" fill="#355c98" opacity="0"/>
    <polygon points="676,31 714,0 717,0 702,31" fill="#355c98" opacity="0"/>
    <polygon points="676,31 714,0 717,0 702,31" fill="#355c98" opacity="0"/>
    <polygon points="676,31 714,0 717,0 702,31" fill="#355c98" opacity="0"/>
    <polygon points="676,31 714,0 717,0 702,31" fill="#355c98" opacity="0"/>
    <polygon points="676,31 714,0 717,0 702,31" fill="#355c98" opacity="0"/>
    <polygon points="676,31 714,0 717,0 702,31" fill="#355c98" opacity="0"/>
    <polygon points="676,31 714,0 717,0 702,31" fill="#355c98" opacity="0"/>
    <polygon points="676,31 714,0 717,0 702,31" fill="#355c98" opacity="0"/>
    <polygon points="676,31 714,0 717,0 702,31" fill="#355c98" opacity="0"/>
    <polygon points="676,31 714,0 717,0 702,31" fill="#355c98" opacity="0"/>
    <polygon points="676,31 714,0 717,0 702,31" fill="#355c98" opacity="0"/>
    <polygon points="676,31 714,0 717,0 702,31" fill="#355c98" opacity="0"/>
    <polygon points="676,31 714,0 717,0 702,31" fill="#355c98" opacity="0"/>
    <polygon points="676,31 714,0 717,0 702,31" fill="#355c98" opacity="0"/>
    <polygon points="676,31 714,0 717,0 702,31" fill="#355c98" opacity="0"/>
    <polygon points="676,31 714,0 717,0 702,31" fill="#355c98" opacity="0"/>
    <polygon points="676,31 714,0 717,0 702,31" fill="#355c98" opacity="0"/>
    <polygon points="676,31 714,0 717,0 702,31" fill="#355c98" opacity="0"/>
    <polygon points="676,31 714,0 717,0 702,31" fill="#355c98" opacity="0"/>
    <polygon points="676,31 714,0 717,0 702,31" fill="#355c98" opacity="0"/>
    <polygon points="676,31 714,0 717,0 702,31" fill="#355c98" opacity="0"/>
    <polygon points="676,31 714,0 717,0 702,31" fill="#355c98" opacity="0"/>
    <polygon points="676,31 714,0 717,0 702,31" fill="#355c98" opacity="0"/>
    <polygon points="676,31 714,0 717,0 702,31" fill="#355c98" opacity="0"/>
    <polygon points="676,31 714,0 717,0 702,31" fill="#355c98" opacity="0"/>
    <polygon points="676,31 714,0 717,0 702,31" fill="#355c98" opacity="0"/>
    <polygon points="676,31 714,0 717,0 702,31" fill="#355c98" opacity="0"/>
    <polygon points="676,31 714,0 717,0 702,31" fill="#355c98" opacity="0"/>
    <polygon points="676,31 714,0 717,0 702,31" fill="#355c98" opacity="0"/>
    <polygon points="676,31 714,0 717,0 702,31" fill="#355c98" opacity="0"/>
  </svg>

  <div class="brand">
    <span class="brand-dot" aria-hidden="true"></span>
    <span class="brand-name">Parcelwise HQ</span>
  </div>

  <div class="sender">
    <p class="sender-name">Dana Reyes</p>
    <p class="sender-title">Executive Assistant</p>
  </div>

  <div class="backdrop-disc" role="img" aria-label="Large faint brand disc decoration"></div>

  <div class="footer-rule"></div>

  <address class="contact">
    <p>Address : (555) 210-4470, 82 Harbor Lane,</p>
    <p>Fairview, MI 48000</p>
    <p>Tel. : (555) 318-2096</p>
    <p>Email : dreyes@parcelwisehq.example</p>
    <p>Web: www.parcelwisehq.example</p>
  </address>

  <div class="bottom-band"></div>
</div>
</body>
</html>
```